Volbrey Inc Business Card

Looking to get an updated business card for a Contract Machining company (www.volbreyinc.example) - looking for a clean design the portrays the technical nature of the business - colors can follow the website design and be in any combination that makes sense (red black, white, metallic or silver) - logos attached for use also. Would like space for: Name, title, business phone (555 214-3086), cell phone , website (www.volbreyinc.example) - possibly QR code could be integrated for website (designer choice), business address - 418 Harlow Bend, Larkmoor, OH 48199 (cards will be for 4 employees, I will either need to modify a template or I can provide individual information)
Target Market(s)
Aerospace, defense and medical device manufacturing companies that need machining
Industry/Entity Type
Machining for aerospace, defense, medical
Contact Information for Business Card
Name, Title, Business Phone, Cell Phone, email, business website and business address
Look and feel

```html
<!DOCTYPE html>
<html lang="en">
<head>
<meta charset="utf-8">
<title>Volbrey Inc Business Card</title>
<link href="https://fonts.googleapis.com/css2?family=Montserrat:wght@400;500;800&display=swap" rel="stylesheet">
<style>
  :root {
    --page: #d9d9d9;
    --card-black: #161616;
    --brand-red: #b01e24;
    --paper-white: #ffffff;
    --text-light: #f2f2f2;
  }
  * { margin: 0; padding: 0; box-sizing: border-box; }
  html, body {
    width: 1200px; height: 900px; overflow: hidden;
    background: var(--page);
    font-family: "Montserrat", sans-serif;
  }
  .canvas { position: relative; width: 1200px; height: 900px; }
  .card {
    position: absolute; left: 250px; width: 700px; height: 400px;
    border-radius: 28px; overflow: hidden; background: var(--card-black);
    box-shadow: 0 10px 30px rgba(0,0,0,.25);
  }
  .card-back { top: 40px; }
  .card-front { top: 460px; }

  /* back */
  .back-emblem {
    position: absolute; left: 270px; top: 70px; width: 160px; height: 160px;
    border-radius: 50%;
    background: radial-gradient(circle at 35% 30%, #5a5a5a, #1d1d1d 70%);
    box-shadow: 0 0 0 8px #101010, 0 0 0 10px #2c2c2c;
  }
  .back-name {
    position: absolute; left: 0; right: 0; top: 262px; text-align: center;
    font-weight: 800; font-size: 40px; letter-spacing: 1px;
    color: #050505; text-shadow: 0 1px 0 #2b2b2b;
  }

  /* front */
  .front-art { position: absolute; inset: 0; }
  .front-info { position: absolute; left: 40px; top: 48px; color: var(--text-light); }
  .company-name {
    font-weight: 800; font-size: 34px; color: var(--brand-red);
    line-height: 1; letter-spacing: .5px;
  }
  .person { position: relative; margin-top: 34px; padding-left: 20px; }
  .person::before {
    content: ""; position: absolute; left: 0; top: 2px; width: 8px; height: 62px;
    background: var(--brand-red);
  }
  .person-name { font-weight: 800; font-size: 26px; color: var(--brand-red); letter-spacing: .5px; }
  .person-title { font-weight: 500; font-size: 18px; margin-top: 4px; }
  .address { margin-top: 22px; padding-left: 20px; font-size: 17px; line-height: 1.35; }
  .contacts { list-style: none; margin-top: 18px; padding-left: 20px; font-size: 16px; line-height: 1.5; }
  .contacts li { display: flex; align-items: center; gap: 10px; }
  .contacts svg { width: 14px; height: 14px; fill: var(--brand-red); flex: none; }
</style>
</head>
<body>
<div class="canvas">

  <section class="card card-back" aria-label="Card back">
    <div class="back-emblem"></div>
    <div class="back-name">VOLBREY INC</div>
  </section>

  <section class="card card-front" aria-label="Card front">
    <svg class="front-art" viewBox="0 0 700 400" aria-hidden="true">
      <circle cx="530" cy="155" r="210" fill="var(--paper-white)"/>
      <circle cx="530" cy="155" r="158" fill="var(--brand-red)"/>
      <circle cx="530" cy="155" r="132" fill="none" stroke="var(--paper-white)" stroke-width="3"/>
    </svg>

    <div class="front-info">
      <div class="company-name">VOLBREY INC</div>

      <div class="person">
        <div class="person-name">DORIAN HALE</div>
        <div class="person-title">Managing Director</div>
      </div>

      <div class="address">418 Harlow Bend,<br>Larkmoor, OH 48199</div>

      <ul class="contacts">
        <li>
          <svg viewBox="0 0 16 16"><path d="M3.5 1l2.5 3-1.5 2c1 2 3 4 5 5l2-1.5 3 2.5-1.5 2.5C8 15 1 8 1 3.5z"/></svg>
          (555) 214-3086
        </li>
        <li>
          <svg viewBox="0 0 16 16"><path d="M4 0h8a1 1 0 011 1v14a1 1 0 01-1 1H4a1 1 0 01-1-1V1a1 1 0 011-1zm1 2v10h6V2zm3 11a1 1 0 100 2 1 1 0 000-2z"/></svg>
          555-608-1947
        </li>
        <li>
          <svg viewBox="0 0 16 16"><path d="M0 3h16v10H0zm1.5 1.2V12h13V4.2L8 9z"/></svg>
          info@volbreyinc.example
        </li>
        <li>
          <svg viewBox="0 0 16 16"><path d="M8 0a8 8 0 110 16A8 8 0 018 0zm0 1.5a6.5 6.5 0 00-4.6 11.1L5 10l-1-3 3-2 2-3zm2 6l-1 4 3 2a6.5 6.5 0 001-7z"/></svg>
          www.volbreyinc.example
        </li>
      </ul>
    </div>
  </section>

</div>
</body>
</html>
```